Create a new business card

I’m looking to update my business card to make it match the rest of my brand. I will include my current website as well as what my vehicle designs look like, etc..
What my business currently services
Weekly maintenance pool openings / closings
Equipment repair, including pumps, heaters, salt systems, filters, etc.
We install automatic covers and maintain them as well as provide preventative maintenance

I would like to include my name.
Dorian Pelkin.
My title
Owner
My email
Dorian@tidewellnx.com
4015827160
Www.tidewellnx.com

```html
<!DOCTYPE html>
<html lang="en">
<head>
<meta charset="UTF-8">
<title>Tidewell Pool Care – Business Card</title>
<link href="https://fonts.googleapis.com/css2?family=Montserrat:wght@500;600;700;800&display=swap" rel="stylesheet">
<style>
  :root {
    --page: #c4c4c4;
    --white: #ffffff;
    --navy: #1d3a6e;
    --deep-blue: #23558f;
    --mid-blue: #2d82c4;
    --sky-blue: #3fb0e6;
    --orange: #e0581a;
    --ink: #2b2b2b;
    --heading-blue: #5cc3f0;
  }
  * { box-sizing: border-box; margin: 0; padding: 0; }
  html, body { width: 1200px; height: 900px; overflow: hidden; }
  body {
    background: var(--page);
    font-family: "Montserrat", sans-serif;
    display: flex;
    flex-direction: column;
    align-items: center;
    justify-content: center;
    gap: 40px;
  }
  .card {
    position: relative;
    width: 700px;
    height: 400px;
    border-radius: 18px;
    overflow: hidden;
    box-shadow: 0 10px 26px rgba(0,0,0,0.22);
  }

  /* Front */
  .card-front { background: var(--white); }
  .front-art { position: absolute; inset: 0; }
  .identity {
    position: absolute;
    left: 42px;
    top: 112px;
  }
  .person-name {
    font-size: 34px;
    font-weight: 800;
    color: var(--orange);
    letter-spacing: 0.2px;
    line-height: 1.2;
  }
  .person-title {
    font-size: 16px;
    font-weight: 500;
    color: var(--ink);
    margin-top: 2px;
  }
  .contact-list {
    list-style: none;
    margin-top: 22px;
    display: flex;
    flex-direction: column;
    gap: 7px;
  }
  .contact-item {
    display: flex;
    align-items: center;
    gap: 12px;
    font-size: 15px;
    font-weight: 500;
    color: var(--ink);
  }
  .contact-icon { width: 16px; height: 16px; flex: none; }

  .brand-mark {
    position: absolute;
    right: 36px;
    top: 90px;
    display: flex;
    align-items: center;
    gap: 10px;
  }
  .brand-dot {
    width: 34px;
    height: 34px;
    border-radius: 50%;
    background: var(--white);
    flex: none;
  }
  .brand-name {
    font-size: 26px;
    font-weight: 800;
    color: var(--white);
    line-height: 1.1;
  }

  /* Back */
  .card-back { color: var(--white); }
  .water-surface {
    position: absolute;
    inset: 0;
    background:
      radial-gradient(ellipse at 30% 30%, rgba(120,200,240,0.45), transparent 60%),
      radial-gradient(ellipse at 80% 80%, rgba(20,80,150,0.45), transparent 60%),
      linear-gradient(135deg, #2a8fd0 0%, #1f6fb4 50%, #2b9ad6 100%);
  }
  .back-brand {
    position: absolute;
    left: 44px;
    top: 50%;
    transform: translateY(-50%);
    width: 250px;
    display: flex;
    align-items: center;
    gap: 12px;
  }
  .back-brand .brand-dot { width: 40px; height: 40px; }
  .back-brand .brand-name { font-size: 30px; }
  .divider {
    position: absolute;
    left: 322px;
    top: 70px;
    width: 1.5px;
    height: 260px;
    background: rgba(255,255,255,0.75);
  }
  .services {
    position: absolute;
    left: 352px;
    top: 92px;
  }
  .services-title {
    font-size: 24px;
    font-weight: 700;
    color: var(--heading-blue);
    letter-spacing: 0.5px;
    margin-bottom: 10px;
  }
  .services-list {
    list-style: none;
    display: flex;
    flex-direction: column;
    gap: 6px;
  }
  .services-list li {
    font-size: 16.5px;
    font-weight: 500;
    display: flex;
    align-items: center;
    gap: 10px;
  }
  .services-list li::before {
    content: "";
    width: 5px;
    height: 5px;
    border-radius: 50%;
    background: var(--white);
  }
</style>
</head>
<body>

  <section class="card card-front" aria-label="Business card front">
    <svg class="front-art" viewBox="0 0 700 400" width="700" height="400" aria-hidden="true">
      <defs>
        <linearGradient id="swoop-fill" x1="1" y1="0" x2="0" y2="1">
          <stop offset="0" stop-color="#1d3a6e"/>
          <stop offset="0.55" stop-color="#2d7fc1"/>
          <stop offset="1" stop-color="#3fb0e6"/>
        </linearGradient>
      </defs>
      <path d="M450 0 L700 0 L700 400 L140 400 C300 360 400 250 450 0 Z" fill="url(#swoop-fill)"/>
      <path d="M480 0 C450 200 360 330 180 400" fill="none" stroke="#ffffff" stroke-width="7"/>
      <path d="M0 398 C170 392 330 348 420 225 C360 345 200 398 60 400 L0 400 Z" fill="#3fb0e6"/>
      <path d="M0 372 C160 368 320 325 410 195 C360 310 210 372 0 386 Z" fill="#e0581a"/>
    </svg>

    <div class="identity">
      <h1 class="person-name">Dorian Pelkin</h1>
      <p class="person-title">Owner</p>
      <ul class="contact-list">
        <li class="contact-item">
          <svg class="contact-icon" viewBox="0 0 16 16" aria-hidden="true"><path d="M3 1.5h3l1.2 3-1.8 1.2a8 8 0 0 0 4.9 4.9l1.2-1.8 3 1.2v3a1.5 1.5 0 0 1-1.6 1.5A13 13 0 0 1 1.5 3.1 1.5 1.5 0 0 1 3 1.5z" fill="#2d82c4"/></svg>
          4015827160
        </li>
        <li class="contact-item">
          <svg class="contact-icon" viewBox="0 0 16 16" aria-hidden="true"><rect x="1" y="3" width="14" height="10" rx="1.5" fill="#2d82c4"/><path d="M1.5 4 8 9l6.5-5" fill="none" stroke="#fff" stroke-width="1.3"/></svg>
          Dorian@tidewellnx.com
        </li>
        <li class="contact-item">
          <svg class="contact-icon" viewBox="0 0 16 16" aria-hidden="true"><circle cx="8" cy="8" r="7" fill="#2d82c4"/><path d="M1 8h14M8 1c-3 3.5-3 10.5 0 14M8 1c3 3.5 3 10.5 0 14" fill="none" stroke="#fff" stroke-width="1"/></svg>
          Www.tidewellnx.com
        </li>
      </ul>
    </div>

    <div class="brand-mark">
      <span class="brand-dot"></span>
      <span class="brand-name">Tidewell<br>Pool Care</span>
    </div>
  </section>

  <section class="card card-back" aria-label="Business card back">
    <div class="water-surface" role="img" aria-label="Rippling blue swimming pool water"></div>

    <div class="back-brand">
      <span class="brand-dot"></span>
      <span class="brand-name">Tidewell<br>Pool Care</span>
    </div>

    <div class="divider"></div>

    <div class="services">
      <h2 class="services-title">OUR SERVICES</h2>
      <ul class="services-list">
        <li>Pool Opening and Closing</li>
        <li>Renovation</li>
        <li>Weekly pool services</li>
        <li>Electronic Leak detection</li>
        <li>Structural Pool Repair</li>
        <li>Equipment repairs and Upgrades</li>
      </ul>
    </div>
  </section>

</body>
</html>
```